Brookvale Estates LLC stationary for a real estate property management company.

Create stationary (letterhead, envelopes, business cards) using Brookvale Estates LLC logo as primary creative element. Stationary design needs to be horizontal, leaving as much space as possible for correspondence copy. See attached Creative Brief and past stationary files for details.

Target Market(s)

Prospective apartment residents and current residents, vendors, and government agencies.

Industry/Entity Type

Property Management

Contact Information for Business Card

Business card employee title: Property Manager. Should include address, phone, fax, email, website, slogan, and Brookvale Estates logo.

Font styles to use
Sans Serif

Colors
0592cd
000000

Requirements
Must have
• Tone should be conservative, institutional, business (i.e. banking, finance, real estate). Must include: address, phone, fax, website, and slogan (see attached Creative Brief). Should be a horizontal design, leaving as much room as possible for letter correspondence copy.
Nice to have
• Please use an Arial or Helvetica style font.
Should not have
• Letterhead layout should leave as much room as possible for copy.

```html
<!DOCTYPE html>
<html lang="en">
<head>
<meta charset="utf-8">
<title>Brookvale Estates LLC – Business Card</title>
<link rel="stylesheet" href="https://fonts.googleapis.com/css2?family=Arimo:wght@400;700&display=swap">
<style>
  :root {
    --brand-blue: #0a68a6;
    --ink: #4a4a4a;
    --card-white: #f6f6f6;
    --backdrop: #e4e1dc;
    --rule: #c9c9c9;
    --white: #ffffff;
  }
  * { margin: 0; padding: 0; box-sizing: border-box; }
  html, body {
    width: 1200px; height: 960px; overflow: hidden;
    background: var(--backdrop);
    font-family: "Arimo", Arial, Helvetica, sans-serif;
  }
  .canvas { position: relative; width: 1200px; height: 960px; }

  .card {
    position: absolute; width: 600px; height: 342px;
    box-shadow: 0 2px 6px rgba(0,0,0,0.25);
  }
  .card--front { left: 302px; top: 130px; background: var(--card-white); }
  .card--back { left: 299px; top: 488px; background: var(--brand-blue); }

  .wordmark {
    position: absolute; left: 50px; top: 150px;
    display: flex; align-items: center; gap: 10px;
  }
  .wordmark__dot {
    width: 30px; height: 30px; border-radius: 50%;
    background: var(--brand-blue); flex: none;
  }
  .wordmark__name {
    color: var(--brand-blue); font-weight: 700; font-size: 19px;
    white-space: nowrap;
  }

  .divider {
    position: absolute; left: 307px; top: 86px;
    width: 1px; height: 178px; background: var(--rule);
  }

  .contact { position: absolute; left: 330px; top: 86px; color: var(--ink); }
  .contact__name {
    color: var(--brand-blue); font-weight: 700; font-size: 22px;
    line-height: 26px; letter-spacing: 0.2px;
  }
  .contact__title { font-size: 16px; line-height: 20px; margin-bottom: 10px; }
  .contact__address { font-size: 14px; line-height: 19px; margin-bottom: 7px; }
  .contact__list { list-style: none; font-size: 14px; line-height: 19.5px; }
  .contact__list li { display: flex; align-items: center; gap: 8px; }
  .contact__list svg { width: 14px; height: 14px; fill: var(--brand-blue); flex: none; }

  .back-mark {
    position: absolute; left: 0; right: 0; top: 140px;
    display: flex; justify-content: center; align-items: center; gap: 14px;
  }
  .back-mark__dot { width: 40px; height: 40px; border-radius: 50%; background: var(--white); }
  .back-mark__name { color: var(--white); font-weight: 700; font-size: 36px; white-space: nowrap; }

  .slogan {
    position: absolute; left: 0; right: 0; top: 287px;
    text-align: center; color: var(--white);
    font-weight: 700; font-size: 16px;
  }
</style>
</head>
<body>
<main class="canvas">
  <section class="card card--front" aria-label="Business card front">
    <div class="wordmark">
      <span class="wordmark__dot"></span>
      <span class="wordmark__name">Brookvale Estates LLC</span>
    </div>
    <div class="divider"></div>
    <div class="contact">
      <h1 class="contact__name">DANIEL WHITAKER</h1>
      <p class="contact__title">Property Manager</p>
      <p class="contact__address">2780 Harbor Ridge Drive #B210<br>Fairview, CA 92418</p>
      <ul class="contact__list">
        <li>
          <svg viewBox="0 0 16 16" aria-hidden="true"><path d="M3.6 1.2l2.3 2.5-1.2 1.9c.8 1.9 2.5 3.7 4.5 4.6l1.8-1.2 2.6 2.2-1.1 2.4c-5.4-.4-9.9-4.9-10.3-10.4z"/></svg>
          <span>555-214-7730</span>
        </li>
        <li>
          <svg viewBox="0 0 16 16" aria-hidden="true"><path d="M4 1h8v4H4zM1 6h14v6h-2v-2H3v2H1zM4 11h8v4H4z"/></svg>
          <span>555-214-7731</span>
        </li>
        <li>
          <svg viewBox="0 0 16 16" aria-hidden="true"><path d="M1 3h14v1.2L8 9 1 4.2zM1 5.8l7 4.8 7-4.8V13H1z"/></svg>
          <span>daniel@brookvaleestates.us</span>
        </li>
        <li>
          <svg viewBox="0 0 16 16" aria-hidden="true"><path d="M8 1a7 7 0 100 14A7 7 0 008 1zm-1 2.3c-.6.9-1.5 1.4-1.2 2.6.3 1.1 1.9.6 2.2 1.8.2 1-.9 1.6-.6 2.7.2.8 1 1.6.7 2.9A5.2 5.2 0 017 3.3zm3.2 9.5c-.4-1 .4-1.8.2-2.9-.2-.9-1.5-.9-1.4-2 .1-1 1.7-.9 2.3-1.9.3-.5.2-1 0-1.5a5.2 5.2 0 01-1.1 8.3z"/></svg>
          <span>www.brookvaleestates.us</span>
        </li>
      </ul>
    </div>
  </section>

  <section class="card card--back" aria-label="Business card back">
    <div class="back-mark">
      <span class="back-mark__dot"></span>
      <span class="back-mark__name">Brookvale Estates</span>
    </div>
    <p class="slogan">Multifamily Property Management</p>
  </section>
</main>
</body>
</html>
```